Bright Harbor Health Coastal Kickoff Quest advertisement design

We need an advertisement for a health, fitness and wellbeing company promoting a new service. The Coastal Kickoff Quest is a 10 week challenge where people choose from 2 program streams - either 1. Fat Loss or 2. Build Lean Muscle. Access to 40 group functional fitness sessions a week, access to exclusive discounts from Pantry Fuel Depot (PFD), discounts on personal training, a targeted gym program, full gym access for the duration of the Challenge and access to Exercise Physiologists and a Sports Dietitian. This is an Bright Harbor Health service co-branded with Pantry Fuel Depot. The final design should be in line with the style guide, be motivating and communicate a point of difference in the fitness industry.

Target Market(s)

men and women ages 30-50yrs, interested in improving their health and lifestyle

Industry/Entity Type

Fitness

Font styles to use
Other font styles liked:
• see style guide

Colors
000000
5c5c5c
9d9d9d
33b8a4
00a990

Requirements
Must have
• professional and exclusive look and feel, motivating tone
Nice to have
• clean design, not too overcrowding, use key pieces of information only and try to stay within the style guide for colour scheme (what is indicated below is the closest pick to our style guide but colour codes are within)
Should not have
• My project should not have any images that cheapen the challenge to look more like a general gym or body sculpting boot camp

```html
<!DOCTYPE html>
<html lang="en">
<head>
<meta charset="utf-8">
<title>Bright Harbor Health – Coastal Kickoff Quest</title>
<link rel="stylesheet" href="https://fonts.googleapis.com/css2?family=Share+Tech&family=Roboto:wght@300;400;500&display=swap">
<style>
  :root {
    --black: #000000;
    --charcoal: #1a1a1a;
    --grey-dark: #5c5c5c;
    --grey: #9d9d9d;
    --teal: #33b8a4;
    --teal-deep: #00a990;
    --white: #ffffff;
  }
  html, body { margin: 0; padding: 0; overflow: hidden; background: var(--white); }
  .poster {
    position: relative;
    width: 849px;
    height: 1200px;
    overflow: hidden;
    background: var(--white);
    font-family: "Roboto", Arial, sans-serif;
    color: var(--black);
  }
  .header {
    position: absolute; left: 0; top: 0; width: 849px; height: 242px;
    background: var(--black);
  }
  .header-frame {
    position: absolute; left: 22px; top: 22px; right: 22px; bottom: -10px;
    border: 3px solid var(--white); border-bottom: none;
  }
  .kicker {
    position: absolute; left: 0; right: 0; top: 48px;
    text-align: center; color: var(--white);
    font-family: "Share Tech", sans-serif; font-size: 34px; letter-spacing: 4px;
  }
  .headline {
    position: absolute; left: 0; right: 0; top: 100px;
    text-align: center; color: var(--teal);
    font-family: "Share Tech", sans-serif; font-size: 96px; letter-spacing: 12px; line-height: 1;
  }
  .features {
    position: absolute; left: 0; top: 242px; width: 849px; height: 490px;
    background: var(--white);
  }
  .features-frame {
    position: absolute; left: 22px; right: 22px; top: 0; bottom: 0;
    border-left: 3px solid var(--black); border-right: 3px solid var(--black);
  }
  .divider { position: absolute; background: var(--black); }
  .divider.v1 { left: 315px; top: 65px; width: 3px; height: 380px; }
  .divider.v2 { left: 530px; top: 65px; width: 3px; height: 380px; }
  .divider.h-left { left: 85px; top: 223px; width: 228px; height: 2px; }
  .divider.h-right { left: 535px; top: 223px; width: 240px; height: 2px; }
  .feature { position: absolute; text-align: center; line-height: 1; }
  .feature .big { font-family: "Share Tech", sans-serif; letter-spacing: 2px; }
  .teal { color: var(--teal); }
  .f-gym { left: 85px; width: 228px; top: 80px; }
  .f-gym .big { font-size: 52px; }
  .f-gym .sub { font-family: "Share Tech", sans-serif; font-size: 30px; margin-top: 6px; }
  .f-discount { left: 85px; width: 228px; top: 250px; }
  .f-discount .label { font-family: "Share Tech", sans-serif; font-size: 28px; letter-spacing: 1px; }
  .f-discount .small { font-size: 22px; margin-top: 6px; }
  .f-discount .brand { font-family: "Share Tech", sans-serif; font-size: 82px; color: var(--teal); margin-top: 2px; }
  .f-discount .brand-name { font-size: 20px; margin-top: 4px; }
  .f-sessions { left: 318px; width: 212px; top: 130px; }
  .f-sessions .count { font-family: "Share Tech", sans-serif; font-size: 104px; }
  .f-sessions .count span { font-size: 40px; vertical-align: 44px; }
  .f-sessions .group { font-family: "Share Tech", sans-serif; font-size: 40px; color: var(--teal); margin-top: 14px; line-height: 1.05; letter-spacing: 2px; }
  .f-sessions .small { font-family: "Share Tech", sans-serif; font-size: 32px; margin-top: 8px; }
  .f-program { left: 535px; width: 240px; top: 80px; }
  .f-program .label { font-family: "Share Tech", sans-serif; font-size: 36px; letter-spacing: 1px; }
  .f-program .big { font-size: 66px; color: var(--teal); margin-top: 4px; }
  .f-program .small { font-family: "Share Tech", sans-serif; font-size: 32px; margin-top: 2px; }
  .f-experts { left: 535px; width: 240px; top: 260px; }
  .f-experts .big { font-size: 56px; color: var(--teal); }
  .f-experts .small { font-size: 22px; margin-top: 10px; line-height: 1.25; }
  .streams {
    position: absolute; left: 22px; top: 732px; width: 799px; height: 56px;
    background: var(--teal); border: 3px solid var(--charcoal);
    color: var(--white); text-align: center;
    font-family: "Share Tech", sans-serif; font-size: 34px; letter-spacing: 3px; line-height: 56px;
  }
  .streams .or { font-size: 26px; letter-spacing: 1px; }
  .footer {
    position: absolute; left: 0; top: 794px; width: 849px; height: 406px;
    background: var(--black);
  }
  .footer-frame {
    position: absolute; left: 22px; right: 22px; top: 0; bottom: 22px;
    border: 3px solid var(--white); border-top: none;
  }
  .brand-mark {
    position: absolute; left: 0; right: 0; top: 160px;
    text-align: center; color: var(--teal);
    font-family: "Share Tech", sans-serif; font-size: 62px; letter-spacing: 6px;
  }
</style>
</head>
<body>
<main class="poster">
  <header class="header">
    <div class="header-frame"></div>
    <div class="kicker">10-WEEK COASTAL KICKOFF</div>
    <h1 class="headline" style="margin:0;font-weight:400;">QUEST</h1>
  </header>

  <section class="features">
    <div class="features-frame"></div>
    <div class="divider v1"></div>
    <div class="divider v2"></div>
    <div class="divider h-left"></div>
    <div class="divider h-right"></div>

    <div class="feature f-gym">
      <div class="big">FULL</div>
      <div class="big teal">GYM</div>
      <div class="sub teal">ACCESS</div>
    </div>

    <div class="feature f-discount">
      <div class="label">EXCLUSIVE</div>
      <div class="small">Discounts from</div>
      <div class="brand">PFD</div>
      <div class="brand-name">Pantry Fuel Depot</div>
    </div>

    <div class="feature f-sessions">
      <div class="count">40<span>/wk</span></div>
      <div class="group">GROUP<br>FITNESS</div>
      <div class="small">Sessions</div>
    </div>

    <div class="feature f-program">
      <div class="label">TARGETED</div>
      <div class="big">GYM</div>
      <div class="small">Program</div>
    </div>

    <div class="feature f-experts">
      <div class="big">ACCESS</div>
      <div class="small">Exercise Physiologist<br>&amp; Sports Dietician</div>
    </div>
  </section>

  <div class="streams">FAT LOSS <span class="or">or</span> BUILD LEAN MUSCLE</div>

  <footer class="footer">
    <div class="footer-frame"></div>
    <div class="brand-mark">BRIGHT HARBOR HEALTH</div>
  </footer>
</main>
</body>
</html>
```